Moravel Aesthetic Doctor

I require an elegant, luxurious looking business card for my aesthetic business. I am a doctor and that will set me aside from competitors. I am planning to provide home and spa based treatments to clients with high expectations. I have attached my logo.

```html
<!DOCTYPE html>
<html lang="en">
<head>
<meta charset="utf-8">
<title>Moravel Aesthetic Doctor – Business Card</title>
<link rel="stylesheet" href="https://fonts.googleapis.com/css2?family=Roboto:ital,wght@0,300;0,400;1,400&display=swap">
<style>
  :root {
    --backdrop: #3a3a3c;
    --card: #222224;
    --card-edge: #2b2b2e;
    --ink-light: #c9cbcf;
    --ink-muted: #9a9ca1;
    --accent-blue: #52b5ea;
    --band-grey: #a6acb7;
    --band-black: #141416;
    --white: #ffffff;
  }
  * { margin: 0; padding: 0; box-sizing: border-box; }
  html, body {
    width: 799px; height: 1200px; overflow: hidden;
    background: var(--backdrop);
    font-family: "Roboto", Arial, sans-serif;
  }
  .sheet {
    position: relative; width: 799px; height: 1200px;
    display: flex; flex-direction: column; align-items: center; justify-content: space-around;
    padding: 60px 0;
  }
  .card {
    position: relative; width: 640px; height: 366px;
    background: var(--card);
    border: 1px solid var(--card-edge);
    box-shadow: 0 12px 30px rgba(0,0,0,0.45);
    overflow: hidden;
  }
  /* Front */
  .card-front { display: flex; align-items: center; justify-content: center; }
  .front-mark { display: flex; align-items: center; gap: 16px; }
  .front-mark .dot {
    width: 22px; height: 22px; border-radius: 50%;
    border: 2px solid var(--ink-muted);
  }
  .front-mark .brand {
    font-weight: 300; font-size: 30px; letter-spacing: 2px;
    color: var(--ink-muted);
  }
  /* Back */
  .waves { position: absolute; inset: 0; }
  .identity { position: absolute; left: 40px; top: 34px; }
  .identity .name { font-weight: 300; font-size: 25px; color: var(--ink-light); }
  .identity .letters { font-style: italic; font-size: 12px; color: var(--accent-blue); margin-top: 4px; }
  .identity .diploma { font-size: 15px; line-height: 1.25; color: var(--accent-blue); margin-top: 6px; }
  .contacts { position: absolute; left: 40px; top: 156px; font-size: 14px; color: var(--ink-light); }
  .contacts li { list-style: none; display: flex; align-items: center; gap: 8px; height: 21px; }
  .contacts svg { width: 13px; height: 13px; fill: var(--ink-light); }
  .social { display: inline-flex; gap: 5px; margin-left: 6px; }
  .social span { width: 14px; height: 14px; border-radius: 50%; background: var(--white); display: inline-block; }
  .website {
    position: absolute; left: 300px; top: 198px; font-size: 14px; color: var(--ink-light);
    display: flex; align-items: center; gap: 8px;
  }
  .website svg { width: 13px; height: 13px; }
  .back-mark {
    position: absolute; right: 40px; top: 112px;
    display: flex; align-items: center; gap: 14px;
  }
  .back-mark .dot { width: 26px; height: 26px; border-radius: 50%; border: 2px solid var(--ink-light); }
  .back-mark .brand { font-weight: 400; color: var(--ink-light); line-height: 1.05; }
  .back-mark .brand .line1 { display: block; font-size: 40px; letter-spacing: 1px; }
  .back-mark .brand .line2 { display: block; font-size: 16px; letter-spacing: 2px; }
  .tagline {
    position: absolute; right: 40px; bottom: 18px; text-align: right;
    font-size: 17px; line-height: 1.25; color: var(--white);
  }
</style>
</head>
<body>
<main class="sheet">
  <section class="card card-front" aria-label="Card front">
    <div class="front-mark">
      <span class="dot"></span>
      <span class="brand">Moravel Aesthetic Doctor</span>
    </div>
  </section>

  <section class="card card-back" aria-label="Card back">
    <svg class="waves" viewBox="0 0 640 366" preserveAspectRatio="none" aria-hidden="true">
      <path d="M0,238 C160,244 330,318 640,270 L640,282 C330,330 160,254 0,252 Z" fill="var(--band-grey)"/>
      <path d="M0,252 C160,254 330,330 640,282 L640,296 C330,344 160,268 0,266 Z" fill="var(--band-black)"/>
      <path d="M0,266 C160,268 330,344 640,296 L640,366 L0,366 Z" fill="var(--accent-blue)"/>
    </svg>

    <div class="identity">
      <p class="name">Dr Elise Varden</p>
      <p class="letters">MRCPCH MD</p>
      <p class="diploma">Australasian Diploma of<br>Aesthetic Medicine</p>
    </div>

    <ul class="contacts">
      <li><svg viewBox="0 0 16 16"><path d="M1 3h14v10H1z M1 3l7 6 7-6" fill="none" stroke="var(--ink-light)" stroke-width="1.6"/></svg>elise@moravel.co.nz</li>
      <li><svg viewBox="0 0 16 16"><path d="M4 1l3 3-2 2c1 2 3 4 5 5l2-2 3 3-2 3C7 15 1 9 1 3z"/></svg>0800 555 014</li>
      <li>Follow us on:<span class="social"><span></span><span></span></span></li>
    </ul>

    <div class="website">
      <svg viewBox="0 0 16 16"><g fill="none" stroke="var(--ink-light)" stroke-width="1.3"><circle cx="8" cy="8" r="6.5"/><ellipse cx="8" cy="8" rx="3" ry="6.5"/><path d="M1.5 8h13"/></g></svg>
      www.moravel.co.nz
    </div>

    <div class="back-mark">
      <span class="dot"></span>
      <p class="brand"><span class="line1">MORAVEL</span><span class="line2">AESTHETIC DOCTOR</span></p>
    </div>

    <p class="tagline">Home and Spa<br>Based Treatments</p>
  </section>
</main>
</body>
</html>
```